Crowler Can Label for a Brewery Beer Can

Creating a label for our brewery's Crowler Can. Our area is know for mountains, glaciers, and the ocean view. We would like to include these in the drawing. Along with our logo. Overall we think more is less. A nice simple label is our preference that is elegant. We included a couple we like, but do not copy them exactly.

There will need to be white room for us to label each can by hand - spaces for - Name, ABV and Date.

The text must be on lable- GOVERNMENT WARNING: (1) According to the Surgeon General, women should not drink alcoholic beverages during pregnancy because of the risk of birth defects. (2) Consumption of alcoholic beverages impairs your ability to drive a car or operate machinery,and may cause health problems.

We also want our address and website-
287 Brisket Ln, Larchmere Cove 99614
www.fernholtbrewing.example

Also needs to have size on the label - 32 Fluid Oz

Getting some great designs, but be good for more time for some designers to rework with suggestions given.

Colors

Designer to choose colors to be used in the design.

Requirements
Must have
• I included the label size template in the graphics. Must be this size.
• There will need to be white room for us to label each can by hand - spaces for - Name, ABV and Date.
• The text must be on lable- GOVERNMENT WARNING: (1) According to the Surgeon General, women should not drink alcoholic beverages during pregnancy because of the risk of birth defects. (2) Consumption of alcoholic beverages impairs your ability to drive a car or operate machinery,and may cause health problems.
• We also want our address and website-
• 287 Brisket Ln, Larchmere Cove 99614
• www.fernholtbrewing.example
• Needs to have size on the label - 32 Fl Oz
Nice to have
• Mountains, Glacier and ocean scene.

```html
<!DOCTYPE html>
<html lang="en">
<head>
<meta charset="utf-8">
<title>Fernholt Brewing – Crowler Label</title>
<link rel="stylesheet" href="https://fonts.googleapis.com/css2?family=Montserrat:wght@800&family=Pinyon+Script&family=Passion+One:wght@400&family=Poppins:wght@800&family=Open+Sans:wght@400;700&display=swap">
<style>
  :root {
    --backdrop-top: #c4cad4;
    --backdrop-bottom: #b6c4da;
    --label-top: #f2f5fa;
    --label-bottom: #dfe6f0;
    --ink-navy: #161a4f;
    --ink-violet: #2c2660;
    --field-fill: rgba(255,255,255,0.55);
    --scene-sky: #e6ecf6;
    --scene-peak: #7b95cf;
    --scene-snow: #f4f6fa;
  }
  * { box-sizing: border-box; margin: 0; padding: 0; }
  html, body { width: 1200px; height: 900px; overflow: hidden; }
  body {
    position: relative;
    background: linear-gradient(180deg, var(--backdrop-top), var(--backdrop-bottom));
    font-family: "Open Sans", sans-serif;
  }
  .label-panel {
    position: absolute;
    top: 84px;
    width: 356px;
    height: 676px;
    border-radius: 18px;
    overflow: hidden;
    background: linear-gradient(180deg, var(--label-top), var(--label-bottom));
  }
  .label-front { left: 192px; }
  .label-back { left: 708px; }

  .landscape-art {
    position: absolute;
    left: 0; right: 0; bottom: 0;
    background: linear-gradient(180deg, var(--scene-sky) 0%, var(--scene-peak) 35%, #9fb2dc 60%, var(--scene-snow) 100%);
  }
  .label-front .landscape-art { top: 480px; }
  .label-back .landscape-art { top: 580px; }

  .brand-mark {
    position: absolute;
    top: 90px; left: 0; right: 0;
    display: flex; flex-direction: column; align-items: center; gap: 18px;
  }
  .brand-dot {
    width: 110px; height: 110px; border-radius: 50%;
    background: var(--ink-navy);
  }
  .brand-name {
    font-family: "Montserrat", sans-serif;
    font-weight: 800;
    font-size: 30px;
    letter-spacing: 1px;
    color: var(--ink-navy);
    text-align: center;
    line-height: 1.1;
  }
  .product-title {
    position: absolute;
    top: 362px; left: 0; right: 0;
    text-align: center;
    font-family: "Pinyon Script", cursive;
    font-size: 48px;
    color: var(--ink-navy);
    transform: rotate(-4deg);
  }
  .volume {
    position: absolute;
    top: 440px; left: 0; right: 0;
    text-align: center;
    font-family: "Passion One", sans-serif;
    font-size: 22px;
    color: var(--ink-navy);
  }

  .write-in-field {
    position: absolute;
    left: 18px; right: 18px;
    height: 82px;
    border-radius: 16px;
    background: var(--field-fill);
    display: flex; align-items: center;
    padding-left: 16px;
    font-family: "Poppins", sans-serif;
    font-weight: 800;
    font-size: 17px;
    color: var(--ink-violet);
  }
  .field-name { top: 66px; }
  .field-abv { top: 158px; }
  .field-date { top: 250px; }

  .contact-lines {
    position: absolute;
    top: 342px; left: 0; right: 0;
    text-align: center;
    font-weight: 700;
    font-size: 13.5px;
    line-height: 21px;
    color: var(--ink-navy);
  }
  .government-warning {
    position: absolute;
    top: 390px; left: 18px; right: 18px;
    height: 172px;
    border-radius: 18px;
    background: rgba(255,255,255,0.55);
    padding: 6px 14px;
    font-size: 12.6px;
    line-height: 20px;
    color: var(--ink-violet);
    text-align: justify;
    z-index: 1;
  }
  .warning-heading {
    display: block;
    text-align: center;
    font-weight: 700;
    font-size: 13.5px;
  }
</style>
</head>
<body>
  <section class="label-panel label-front">
    <div class="brand-mark">
      <div class="brand-dot"></div>
      <div class="brand-name">FERNHOLT<br>BREWING</div>
    </div>
    <div class="product-title">Brewery's Crowler</div>
    <div class="volume">32 FLUID OZ</div>
    <div class="landscape-art" role="img" aria-label="Illustration of snowy mountains, glacier, evergreen trees and a winding river"></div>
  </section>

  <section class="label-panel label-back">
    <div class="write-in-field field-name">NAME:</div>
    <div class="write-in-field field-abv">ABV:</div>
    <div class="write-in-field field-date">DATE:</div>
    <div class="contact-lines">
      287 Brisket Ln, Larchmere Cove 99614<br>
      www.fernholtbrewing.example
    </div>
    <div class="government-warning">
      <span class="warning-heading">GOVERNMENT WARNING:</span>
      (1) According to the Surgeon General, women should not drink alcoholic beverages during pregnancy because of the risk of birth defects.<br>
      (2) Consumption of alcoholic beverages impairs your ability to drive a car or operate machinery, and may cause health problems.
    </div>
    <div class="landscape-art" role="img" aria-label="Illustration of snowy hills, evergreen trees and a winding river"></div>
  </section>
</body>
</html>
```